New Business Card Design Project

Use the flyer uploaded and website www.brightoakbuilders.com for inspiration.
List Our Services on Backside of business cards
Marcus Delling
Harborline Builders Inc.
Licensed General Contractors
858-471-6093

Contact Information for Business Card

Use the flyer uploaded and website www.brightoakbuilders.com for inspiration. List Our Services on Backside of business cards Marcus Delling Harborline Builders Inc. Licensed General Contractors 858-471-6093

```html
<!DOCTYPE html>
<html lang="en">
<head>
<meta charset="utf-8">
<title>Harborline Builders – Business Cards</title>
<link href="https://fonts.googleapis.com/css2?family=Oswald:wght@500;600&family=Montserrat:wght@400;500&display=swap" rel="stylesheet">
<style>
  :root{
    --bg:#d9d9d9;
    --card:#ffffff;
    --ink:#141414;
    --band:#131313;
    --red:#e3141b;
    --blue:#3a86cf;
    --photo-a:#e9eeee;
    --photo-b:#b9cfcc;
    --sketch-a:#ffffff;
    --sketch-b:#b8b8b8;
  }
  *{box-sizing:border-box;margin:0;padding:0}
  html,body{width:1200px;height:800px;overflow:hidden}
  body{background:var(--bg);display:flex;align-items:center;justify-content:center;gap:40px;font-family:"Montserrat",sans-serif;color:var(--ink)}
  .card{position:relative;width:540px;height:309px;background:var(--card);overflow:hidden;box-shadow:0 10px 24px rgba(0,0,0,.25)}
  .card-art{position:absolute;inset:0;width:100%;height:100%}
  .brand{position:absolute;display:flex;align-items:center;gap:10px;color:#fff;font-family:"Montserrat",sans-serif;font-weight:400;font-size:19px;letter-spacing:.06em;text-transform:uppercase}
  .brand-dot{width:12px;height:12px;border:1.5px solid #fff;border-radius:50%}
  .front .brand{left:40px;bottom:34px}
  .back .brand{left:150px;bottom:30px}

  .contact{position:absolute;right:28px;top:18px;text-align:right}
  .contact-name{font-family:"Oswald",sans-serif;font-weight:600;font-size:30px;color:var(--red);letter-spacing:.01em;line-height:1.1;margin-bottom:6px}
  .contact-line{display:flex;justify-content:flex-end;align-items:center;gap:8px;font-size:13px;line-height:1.4}
  .contact-line svg{width:12px;height:12px;flex:none}
  .company{margin-top:8px;color:var(--red);font-size:13px;line-height:1.4}

  .services-head{position:absolute;right:22px;top:18px;text-align:right}
  .guarantee{font-family:"Oswald",sans-serif;font-weight:600;font-size:20px;color:var(--red);letter-spacing:.01em;line-height:1.1}
  .ribbon{display:inline-block;margin-top:4px;background:var(--blue);color:#fff;font-family:"Oswald",sans-serif;font-weight:500;font-size:16px;letter-spacing:.03em;padding:1px 16px 1px 50px;clip-path:polygon(12% 0,100% 0,100% 100%,0 100%)}
  .service-list{position:absolute;right:22px;top:82px;list-style:none;text-align:right}
  .service-list li{font-size:12px;line-height:1.3;display:flex;justify-content:flex-end;align-items:center;gap:8px}
  .service-list li::after{content:"";width:7px;height:7px;border-radius:50%;background:var(--red);flex:none}
</style>
</head>
<body>

<section class="card front" aria-label="Business card front">
  <svg class="card-art" viewBox="0 0 540 309" preserveAspectRatio="none">
    <defs>
      <linearGradient id="photoTone" x1="0" y1="0" x2="1" y2="1">
        <stop offset="0" stop-color="var(--photo-a)"/>
        <stop offset="1" stop-color="var(--photo-b)"/>
      </linearGradient>
    </defs>
    <polygon points="0,0 200,0 130,309 0,309" fill="url(#photoTone)" role="img" aria-label="Photo of a bright remodeled bathroom with glass shower"/>
    <polygon points="0,252 540,178 540,309 0,309" fill="var(--band)"/>
    <line x1="0" y1="307.5" x2="540" y2="307.5" stroke="var(--blue)" stroke-width="3"/>
  </svg>

  <div class="contact">
    <h1 class="contact-name">MARCUS DELLING</h1>
    <p class="contact-line">858-471-6093
      <svg viewBox="0 0 16 16"><path d="M4 1.5l2.2 3-1.4 1.6a8 8 0 0 0 5.1 5.1l1.6-1.4 3 2.2-1.3 2.4C7.4 14.4 1.6 8.6 1.6 2.8z" fill="var(--blue)"/></svg>
    </p>
    <p class="contact-line">info@harborlinebuilders.com
      <svg viewBox="0 0 16 16"><rect x="1" y="3" width="14" height="10" fill="var(--blue)"/><path d="M1 3l7 6 7-6" fill="none" stroke="#fff" stroke-width="1.2"/></svg>
    </p>
    <p class="contact-line">www.brightoakbuilders.com
      <svg viewBox="0 0 16 16"><circle cx="8" cy="8" r="7" fill="var(--blue)"/><path d="M1 8h14M8 1c-3 3.5-3 10.5 0 14M8 1c3 3.5 3 10.5 0 14" fill="none" stroke="#fff" stroke-width="1"/></svg>
    </p>
    <p class="company">Harborline Builders Inc.<br>Licensed General Contractors</p>
  </div>

  <div class="brand"><span class="brand-dot"></span>Harborline Builders</div>
</section>

<section class="card back" aria-label="Business card back">
  <svg class="card-art" viewBox="0 0 540 309" preserveAspectRatio="none">
    <defs>
      <linearGradient id="sketchTone" x1="0" y1="1" x2="1" y2="0">
        <stop offset="0" stop-color="var(--sketch-b)"/>
        <stop offset="1" stop-color="var(--sketch-a)"/>
      </linearGradient>
    </defs>
    <polygon points="0,0 230,0 70,220 0,226" fill="url(#sketchTone)" opacity=".7" role="img" aria-label="Faded architectural sketch of a house"/>
    <polygon points="0,226 540,238 540,309 0,309" fill="var(--band)"/>
    <line x1="0" y1="307.5" x2="540" y2="307.5" stroke="var(--blue)" stroke-width="3"/>
  </svg>

  <div class="services-head">
    <h2 class="guarantee">OUR SERVICES ARE 100% GUARENTEED</h2>
    <span class="ribbon">SPECIALIZING IN</span>
  </div>

  <ul class="service-list">
    <li>Remodel: Kitchen &amp; Bath</li>
    <li>Painting: Interior &amp; Exterior</li>
    <li>Flooring: Carpet, Vinyl, Wood</li>
    <li>Window &amp; Door Replacement</li>
    <li>Plumbing: Repairs &amp; Upgrades</li>
    <li>Energy-Efficient Upgrades</li>
    <li>Deck &amp; Patio Construction</li>
    <li>Water &amp; Mold Damage</li>
    <li>Garage Renovation</li>
  </ul>

  <div class="brand"><span class="brand-dot"></span>Harborline Builders</div>
</section>

</body>
</html>
```